Business Card for Multi-Brand Sportswear Company

We are looking for a business card which represents our company and the multiple brands within it.

The company: Fen Athletics (LTD)
The brands: Fen, TavaPuni, ElmStretch, Grit and Rain

Employees using these cards would be representing Fen Athletics, rather than any of the individual brands. You will see a current design within the uploaded files, to give some inspiration. The actual text of the brands is not necessary, but the logos should be on there is some format.

Our creative minds on this are stretched, so we are looking for someone to make this their own, and show us what a good business card should look like.

We may like to get these printed with spot gloss, so keep that in mind with your designs.

www.fenathletics.co.uk

Industry/Entity Type

Business

Contact Information for Business Card

Leo Pemberton-Hale
Operations Manager
(+44) 1632 960 418
Leo@fenathletics.co.uk
www.fenathletics.co.uk

Font styles to use
Sans Serif
Other font styles liked:
• Eurostile

Colors
ffffff

Requirements
Nice to have
• Dark (black) background

```html
<!DOCTYPE html>
<html lang="en">
<head>
<meta charset="utf-8">
<title>Fen Athletics – Business Card</title>
<link href="https://fonts.googleapis.com/css2?family=Exo+2:wght@400;700&family=Michroma&display=swap" rel="stylesheet">
<style>
  :root{
    --bg:#d9d6d2;
    --card:#000000;
    --white:#ffffff;
    --red:#e2231a;
    --grey:#c9c9c9;
    --gloss-dark:#2a2727;
    --gloss-light:#4a4545;
    --brand-a:#6a5a78;
    --brand-b:#e2231a;
    --brand-c:#f07a4a;
  }
  *{margin:0;padding:0;box-sizing:border-box}
  html,body{width:1200px;height:843px;overflow:hidden;background:var(--bg)}
  .canvas{position:relative;width:1200px;height:843px}
  .card{position:absolute;top:251px;width:558px;height:320px;background:var(--card);overflow:hidden;
        font-family:"Exo 2",sans-serif;color:var(--white);box-shadow:0 4px 14px rgba(0,0,0,.35)}
  .card--front{left:28px}
  .card--back{left:614px}
  .gloss{position:absolute;inset:0;width:100%;height:100%}

  .wordmark{position:absolute;left:60px;top:78px;width:223px;text-align:right;
            font-family:"Michroma",sans-serif;font-size:56px;line-height:1;color:var(--white);letter-spacing:2px}
  .holder{position:absolute;right:276px;top:168px;text-align:right}
  .holder__name{font-size:19px;font-weight:700;line-height:24px}
  .holder__role{font-size:16px;color:var(--red);line-height:22px}
  .divider{position:absolute;left:297px;top:107px;width:1px;height:103px;background:var(--white);opacity:.8}

  .contact{position:absolute;left:312px;top:102px;font-size:16px;line-height:21px}
  .contact__address{margin-bottom:4px}
  .contact__row{display:flex;align-items:center;gap:4px;line-height:22px}
  .contact__icon{width:12px;height:12px;flex:none}

  .brands{position:absolute;left:0;top:276px;width:420px;height:24px}
  .brand{position:absolute;top:0;transform:translateX(-50%);font-size:12px;white-space:nowrap;line-height:24px}
  .brand--tava{left:175px;color:var(--brand-a)}
  .brand--grit{left:284px;color:var(--brand-b)}
  .brand--elm{left:380px;color:var(--brand-c)}

  .lockup{position:absolute;right:36px;top:218px;display:flex;align-items:flex-end;gap:10px;color:var(--grey)}
  .lockup__mark{font-family:"Michroma",sans-serif;font-size:52px;line-height:1}
  .lockup__text{display:flex;flex-direction:column;padding-bottom:4px}
  .lockup__name{font-family:"Michroma",sans-serif;font-size:24px;line-height:1;letter-spacing:1px}
  .lockup__tag{font-size:10px;letter-spacing:2.5px;margin-top:6px}
</style>
</head>
<body>
<div class="canvas">

  <section class="card card--front" aria-label="Business card front">
    <svg class="gloss" viewBox="0 0 558 320" aria-hidden="true">
      <defs>
        <linearGradient id="cornerGloss" x1="0" y1="1" x2="1" y2="0">
          <stop offset="0" stop-color="var(--gloss-light)"/>
          <stop offset="1" stop-color="#100f0f"/>
        </linearGradient>
      </defs>
      <path d="M415 320 L558 190 L558 320 Z" fill="url(#cornerGloss)"/>
    </svg>

    <div class="wordmark">Fen</div>
    <div class="holder">
      <div class="holder__name">Leo Pemberton-Hale</div>
      <div class="holder__role">Operations Manager</div>
    </div>
    <div class="divider"></div>

    <div class="contact">
      <div class="contact__address">Ashby Lane, Kirkwell<br>Dalton, ZZ1 4QT</div>
      <div class="contact__row">
        <svg class="contact__icon" viewBox="0 0 12 12" aria-hidden="true"><circle cx="6" cy="6" r="6" fill="var(--red)"/><path d="M3.5 3h1.6l.6 1.6-.9.7a4 4 0 0 0 2 2l.7-.9 1.6.6V8.6A.8.8 0 0 1 8.2 9.4 5.6 5.6 0 0 1 3 4 .8.8 0 0 1 3.5 3z" fill="#000"/></svg>
        <span>(+44) 1632 960 418</span>
      </div>
      <div class="contact__row">
        <svg class="contact__icon" viewBox="0 0 12 12" aria-hidden="true"><circle cx="6" cy="6" r="6" fill="var(--red)"/><rect x="3" y="4" width="6" height="4.2" fill="none" stroke="#000" stroke-width=".9"/><path d="M3 4l3 2.3L9 4" fill="none" stroke="#000" stroke-width=".9"/></svg>
        <span>Leo@fenathletics.co.uk</span>
      </div>
      <div class="contact__row">
        <svg class="contact__icon" viewBox="0 0 12 12" aria-hidden="true"><circle cx="6" cy="6" r="6" fill="var(--red)"/><circle cx="6" cy="6" r="3.2" fill="none" stroke="#000" stroke-width=".8"/><path d="M2.8 6h6.4M6 2.8v6.4" stroke="#000" stroke-width=".8"/></svg>
        <span>www.fenathletics.co.uk</span>
      </div>
    </div>

    <div class="brands">
      <span class="brand brand--tava">TavaPuni</span>
      <span class="brand brand--grit">Grit and Rain</span>
      <span class="brand brand--elm">ElmStretch</span>
    </div>
  </section>

  <section class="card card--back" aria-label="Business card back">
    <svg class="gloss" viewBox="0 0 558 320" aria-hidden="true">
      <defs>
        <linearGradient id="leafGloss" x1="0" y1="1" x2="1" y2="0">
          <stop offset="0" stop-color="#141313"/>
          <stop offset=".45" stop-color="var(--gloss-dark)"/>
          <stop offset="1" stop-color="var(--gloss-light)"/>
        </linearGradient>
      </defs>
      <path d="M0 187 C70 130 120 70 150 58 C230 18 340 4 431 2 L200 200 C140 255 60 305 0 315 Z" fill="url(#leafGloss)"/>
    </svg>

    <div class="lockup">
      <span class="lockup__mark">Fen</span>
      <div class="lockup__text">
        <span class="lockup__name">ATHLETICS</span>
        <span class="lockup__tag">PERFORMANCE WEAR</span>
      </div>
    </div>
  </section>

</div>
</body>
</html>
```